Stylish new business card needed!

Hello everyone! I am in need of a new business card design for an alarm company here in Hurricane WV. I have all fonts, color codes and logos provided for you use! We are a young company and like the style of a clean sleek looking business card. Would like it double sided, one side holding the logo and the other with your design!
Target Market(s)
The people that are looking for the newest tech for home automation and security
Industry/Entity Type
Alarm services; Home automation
Contact Information for Business Card
Name of person; position (Sales; Installer); Phone Number (555.418.7260); Employee cell Number; Website (www.GuardedByVelk.example); Employee Email; Double sided
Look and feel
Each slider illustrates characteristics of the customer's brand and the style your logo design should communicate.

```html
<!DOCTYPE html>
<html lang="en">
<head>
<meta charset="utf-8">
<title>Guarded By Velk – Business Card</title>
<link href="https://fonts.googleapis.com/css2?family=Lato:wght@400;700;900&display=swap" rel="stylesheet">
<style>
  :root {
    --backdrop: #3a3a3c;
    --card: #2a2b2d;
    --card-deep: #1c1d1f;
    --orange: #f28a3c;
    --grey: #9a9a9a;
    --white: #f4f4f4;
  }
  * { margin: 0; padding: 0; box-sizing: border-box; }
  html, body {
    width: 1200px; height: 937px; overflow: hidden;
    background: var(--backdrop);
    font-family: "Lato", sans-serif;
  }
  .stage { position: relative; width: 1200px; height: 937px; }
  .card {
    position: absolute;
    width: 580px; height: 331px;
    background: var(--card);
    border-radius: 3px;
  }
  .card--back { left: 70px; top: 70px; }
  .card--front { left: 550px; top: 536px; }

  .wordmark {
    position: absolute;
    font-weight: 900;
    text-transform: uppercase;
    line-height: 1;
    text-align: center;
  }
  .wordmark__name { display: block; font-size: 58px; letter-spacing: 1px; }
  .wordmark__tagline { display: block; font-size: 10.5px; letter-spacing: 1.2px; margin-top: 10px; }

  .card--back .wordmark { left: 0; right: 0; top: 122px; color: var(--card-deep); }

  .card--front .wordmark { left: 28px; width: 270px; top: 138px; color: var(--orange); }
  .card--front .wordmark__name { font-size: 40px; }
  .card--front .wordmark__tagline { font-size: 8px; letter-spacing: 0.8px; }

  .divider {
    position: absolute; left: 312px; top: 92px;
    width: 1.5px; height: 150px; background: var(--orange);
  }

  .contact { position: absolute; left: 334px; top: 94px; color: var(--white); }
  .contact__name { font-weight: 900; font-size: 24px; color: var(--orange); letter-spacing: 0.5px; text-transform: uppercase; }
  .contact__role { font-size: 13px; margin-top: 1px; }
  .contact__list { list-style: none; margin-top: 14px; }
  .contact__item { display: flex; align-items: center; gap: 7px; font-size: 13px; line-height: 1.6; }
  .contact__item--plain { padding-left: 17px; }
  .contact__icon { width: 10px; height: 11px; fill: var(--orange); flex: none; }
</style>
</head>
<body>
<main class="stage">
  <section class="card card--back" aria-label="Card back">
    <div class="wordmark">
      <span class="wordmark__name">Guarded By Velk</span>
      <span class="wordmark__tagline">Automation and Security Services</span>
    </div>
  </section>

  <section class="card card--front" aria-label="Card front">
    <div class="wordmark">
      <span class="wordmark__name">Guarded By Velk</span>
      <span class="wordmark__tagline">Automation and Security Services</span>
    </div>

    <div class="divider"></div>

    <div class="contact">
      <p class="contact__name">Dale Harwick</p>
      <p class="contact__role">Manager</p>
      <ul class="contact__list">
        <li class="contact__item contact__item--plain">000-000-0000</li>
        <li class="contact__item">
          <svg class="contact__icon" viewBox="0 0 10 11"><rect x="1.5" y="0.5" width="7" height="10" rx="1.2" fill="none" stroke="var(--orange)" stroke-width="1.2"/><rect x="4" y="8.3" width="2" height="1" /></svg>
          555.418.7260
        </li>
        <li class="contact__item">
          <svg class="contact__icon" viewBox="0 0 10 11"><path d="M2 1 L4 1 L4.8 3.4 L3.6 4.4 C4.2 5.8 5.2 6.8 6.6 7.4 L7.6 6.2 L10 7 L10 9 C10 9.6 9.6 10 9 10 C4.8 10 1 6.2 1 2 C1 1.4 1.4 1 2 1 Z"/></svg>
          mail@GuardedByVelk.example
        </li>
        <li class="contact__item">
          <svg class="contact__icon" viewBox="0 0 10 11"><path d="M0.5 2.5 H9.5 V9 H0.5 Z M0.5 2.5 L5 6 L9.5 2.5" fill="none" stroke="var(--orange)" stroke-width="1.2"/></svg>
          www.GuardedByVelk.example
        </li>
      </ul>
    </div>
  </section>
</main>
</body>
</html>
```